Commercial Real Estate Corporate Site

Our company sells an ERP software to Commercial Real Estate Companies, this project is part of a marketing and sales relaunch of the company.

See attached for PDF formatted Design brief

The software is a modular system where client’s can adopt one module at a time. Our customers are corporate clients who own between 10M and 10B of real estate properties. The typical customer is from the IT or the Financial arm of the company. Our differentiation in the market is that our system is built on a no-code environment, so making changes for the client is quick. Incumbents in the market have long implementation cycles, and customization is often not possible. Competitors are Quorvel, TKB, PlotNest, Vumora.

We need a design for our site which will be implemented into Brevo Forge. **All designs must be compatible with the newest version of Brevo Forge.**

We have produced the following attached assets to use in the website design.:

1. Logo
2. Brand Guidelines
3. Content for Pages
4. Menu Structures
5. Illustrations (modules)
I can't attach them because the files are too big, so they're in this google drive instead:
https://files.examplestore.net/share/k29Xa7Lq0Pz3Rt8MwB5nYc4Hv1Jd6Fe?mode=view

The mechanic for our sales process is as follows:

1. We find on module from our application that a client is interested in. The illustrations that we’ve attached represent the individual modules (elements) of the software.
1. For instance, one of our current customers has purchased a commissions module from us which helps calculate the commission that brokers receive for buying and selling their properties.
2. We provide immense value through the module, and then keep in sales communication with the client to determine which other modules we can implement for them.
1. For instance, in the example above, the client is so happy with the commissions module that they want to start working with our leasing module as well. In the next business quarter, they also choose to add our financials module to their business systems.

### Logo

Attached

### Brand Guidelines

Attached

We are open to suggestions on the secondary colour palette.

### **Site Copy**

**We require the following pages to be created; For now, we will do one Market Page, one Product Page, and one Platform / Services Page, and we will use those as inspiration to create the other dozen Marketing Pages and 30 or so Product Pages.**

**Homepage**

Attached

**Market Page** - look at the quorvel site under the Office, Industrial, Retail (https://www.quorvel.com/products/quorvel-commercial-suite/)

**Product** - One product provided, but there will be 30 - look at the vumora page

(https://www.vumora.com/products/general-accounting)

**Platform / Services Page** - pages that tell the story of our platform and services, content to be provided - the platform will use our modules as it highlights the story of the configurability and composability of the platform. Instead of the icons that they use, we want to use our modules.

- https://www.pelbrix.com/enterprise-applications-platform
- https://www.pelbrix.com/cloud-architecture

**Team Page** - just add sample content for starters (6 Team Members to start)

**Schedule Demo Page** - the call to action for all pages

(https://go.vumora.com/schedule-demo.html)

### Menu Structure

The menu is provided as an attachment.

### Illustrations Information

A note about the illustrations - we have provided an illustrator file with the modules, and if you’d like you can arrange the in any way that you’d like to. We especially like when the modules are positioned like a periodic table of the elements.

Our existing clients are

- Torvane Coop - https://www.torvanecoop.com/real-estate/
- Dalsworth Realestate https://dalsworth.com

Our competitors are

- Quorvel - www.quorvel.com
- TKB - [www.tkbsoftware.com](https://www.tkbsoftware.com/) (we don’t like how this one looks)
- Vumora - www.vumora.com
- Plotnest - www.plotnest.com

Design inspiration

- https://lark-studio.brevosite.com/velmo
- Corporate
- Established
- Modern

### Stock Images Guidance

- https://www.drafta.net/design/QXR7Lm2TpWz/Hk9vN3c8Yd41-FbqsaZRr/edit?utm_content=QXR7Lm2TpWz&utm_campaign=designshare&utm_medium=link2&utm_source=sharebutton

Target Market(s)

Commercial Real Estate Companies - they typically own a portfolio of 50 - 5000 real estate properties and need a software to manage it all.

Coding

Coded - Design and coding required

Number of Pages Required

5+ page

Font styles to use
Other font styles liked:
• Fonts defined in brand guideline

Requirements
Must have
• Brevo Forge, Use the Elemental Design, Download ai.zip and png.zip Use Brand Guideline,
Nice to have
• Check design breif

```html
<!DOCTYPE html>
<html lang="en">
<head>
<meta charset="utf-8">
<title>Orbelta — Enterprise Applications Platform for Real Estate</title>
<link rel="stylesheet" href="https://fonts.googleapis.com/css2?family=Orbitron:wght@500;600;700;800&family=Poppins:wght@400;500;600;700&display=swap">
<style>
:root{
  --red:#e4151b;
  --red-dark:#b80f14;
  --ink:#161616;
  --dark:#1b1b1c;
  --dark-2:#232324;
  --grey:#8d8f93;
  --light:#f3f3f3;
  --panel:#ececec;
  --white:#ffffff;
  --text-dim:#d6d6d6;
  --head:'Orbitron',sans-serif;
  --body:'Poppins',sans-serif;
}
*{box-sizing:border-box;margin:0;padding:0}
html,body{width:1200px;height:4194px;overflow:hidden}
body{position:relative;font-family:var(--body);color:var(--ink);background:var(--dark)}
.abs{position:absolute}
a{color:inherit;text-decoration:none}

/* top bar */
.topbar{left:562px;top:0;width:638px;height:32px;background:#1e1e1f;color:var(--white);font-size:12px;display:flex;align-items:center;padding-left:22px;gap:14px}
.topbar .contact{display:flex;align-items:center;gap:6px}
.topbar .social{margin-left:auto;margin-right:28px;display:flex;gap:10px}
.topbar .social span{width:10px;height:10px;border-radius:50%;background:var(--white)}

/* hero */
.hero{left:0;top:0;width:1200px;height:846px;background:linear-gradient(180deg,#b9bbbf 0%,#a7a9ad 30%,#8e9094 48%,#3a3b3d 72%,#1b1b1c 100%)}
.sculpture{left:70px;top:420px;width:1060px;height:400px;border-radius:50%;background:radial-gradient(ellipse at center,rgba(120,122,128,.55) 0%,rgba(70,72,76,.35) 45%,rgba(40,40,42,0) 72%)}
.logo{display:flex;align-items:center;gap:10px;font-family:var(--head);font-weight:800;letter-spacing:2px;white-space:nowrap}
.logo .mark{border:4px solid currentColor}
.site-logo{left:90px;top:36px;color:var(--red);font-size:30px}
.site-logo .mark{width:44px;height:44px}
.nav{left:383px;top:58px;display:flex;align-items:center;gap:14px;font-size:12.5px;font-weight:500;color:var(--ink);white-space:nowrap}
.nav .caret::after{content:"";display:inline-block;margin-left:4px;border:4px solid transparent;border-top-color:var(--red);transform:translateY(2px)}
.btn{display:inline-flex;align-items:center;justify-content:center;font-family:var(--body);font-weight:700;color:var(--white);text-transform:uppercase;white-space:nowrap}
.btn-nav{left:897px;top:45px;width:213px;height:46px;background:var(--red);font-size:13px}
.hero-kicker{left:0;top:180px;width:1200px;text-align:center;font-family:var(--head);font-weight:600;font-size:38px;letter-spacing:4px;color:var(--ink)}
.hero-title{left:0;top:222px;width:1200px;text-align:center;font-family:var(--head);font-weight:800;font-size:104px;letter-spacing:6px;color:var(--red);line-height:1.1}
.hero-sub{left:0;top:355px;width:1200px;text-align:center;font-size:16px;font-weight:600;letter-spacing:-.3px;color:var(--ink)}
.btn-sm{height:36px;font-size:9px}
.btn-learn{left:474px;top:399px;width:102px;background:var(--red)}
.btn-demo{left:583px;top:399px;width:140px;background:var(--ink)}

/* dark section */
.dark{left:0;top:846px;width:1200px;height:1401px;background:linear-gradient(180deg,#1b1b1c 0%,#202021 50%,#1a1a1b 100%)}
.about-media{left:130px;top:925px;width:462px;height:445px}
.about-copy{left:635px;top:978px;width:440px;color:var(--white)}
.h-section{font-family:var(--head);font-weight:700;font-size:42px;letter-spacing:2px;line-height:1.08;white-space:nowrap}
.h-sub{font-family:var(--head);font-weight:600;font-size:14px;letter-spacing:1px;margin:16px 0 14px;white-space:nowrap}
.about-copy p{font-size:13.5px;line-height:1.55;color:var(--text-dim);margin-bottom:12px;letter-spacing:-.2px}
.about-copy b{color:var(--white);font-weight:600}
.modules-head{left:0;top:1462px;width:1200px;text-align:center;color:var(--white)}
.modules-head .h-sub{margin:18px 0 22px;font-size:16px;letter-spacing:2px}
.modules-head p{width:850px;margin:0 auto;font-size:13.5px;line-height:1.55;color:var(--text-dim);letter-spacing:-.2px}
.module-list{left:163px;top:1722px;width:380px;list-style:none;color:var(--white);font-family:var(--head);font-size:12.5px;font-weight:600;letter-spacing:.8px;white-space:nowrap}
.module-list li{height:40px;line-height:40px}
.module-list li.active{color:var(--red);border-bottom:1.5px solid var(--red);display:flex;justify-content:space-between;align-items:center}
.module-cube{left:643px;top:1672px;width:402px;height:441px;border-radius:6px;background:linear-gradient(160deg,#7b7b7d 0%,#626264 55%,#3a3a3b 100%);box-shadow:0 0 60px rgba(0,0,0,.6)}
.link-red{color:var(--red);font-weight:700;font-size:14px;text-decoration:underline;text-underline-offset:4px;display:inline-flex;align-items:center;gap:8px;text-transform:uppercase;white-space:nowrap}
.view-modules{left:510px;top:2162px}

/* light section */
.light{left:0;top:2247px;width:1200px;height:1408px;background:var(--white)}
.platform-img{left:174px;top:2349px;width:366px;height:435px;background:linear-gradient(135deg,#8a8a8d 0%,#5c5c5f 45%,#2e2e30 100%);box-shadow:0 30px 50px rgba(0,0,0,.25)}
.platform-copy{left:602px;top:2386px;width:430px}
.platform-copy .h-sub{font-size:14px;line-height:1.6;margin:22px 0 18px;color:#2b2b2b}
.platform-copy p{font-size:13px;line-height:1.58;color:#555;letter-spacing:-.2px}
.btn-more{margin-top:20px;width:131px;height:46px;background:var(--red);font-size:13px}
.team-panel{left:90px;top:2943px;width:1020px;height:497px;background:var(--panel)}
.team-photo{left:677px;top:2894px;width:368px;height:463px;background:linear-gradient(180deg,#9aa3a8 0%,#c9c2a8 55%,#e7dca0 100%);box-shadow:0 25px 45px rgba(0,0,0,.25)}
.team-copy{left:173px;top:3018px;width:390px}
.team-name{font-family:var(--head);font-weight:600;font-size:20px;letter-spacing:2px;color:var(--red);margin-top:26px}
.team-role{font-size:15px;color:#333;margin-top:2px}
.team-copy p{font-size:12.5px;line-height:1.55;color:#666;margin-top:12px;letter-spacing:-.2px}
.thumbs{display:flex;gap:14px;margin-top:16px}
.thumbs span{width:66px;height:77px;background:linear-gradient(180deg,#c4c7c9,#8f9294)}
.thumbs span:nth-child(2){background:linear-gradient(180deg,#d3d8d2,#9aa39c)}
.thumbs span:nth-child(3){background:linear-gradient(180deg,#b9a99a,#7e7166)}
.thumbs span:nth-child(4){background:linear-gradient(180deg,#d9d6c6,#c8bf7f)}
.team-copy .link-red{margin-top:24px;font-size:14px}

/* footer */
.footer{left:0;top:3655px;width:1200px;height:539px;background:var(--ink)}
.cta{left:158px;top:3520px;width:884px;height:224px;background:linear-gradient(120deg,var(--red) 0%,#ee1e24 55%,#d81117 100%)}
.cta-mark{left:196px;top:3565px;width:150px;height:140px;border:6px solid var(--white)}
.cta-text{left:374px;top:3586px;color:var(--white);font-family:var(--head);font-weight:600;font-size:24px;letter-spacing:3px;line-height:1.3;white-space:nowrap}
.btn-cta{left:799px;top:3606px;width:197px;height:50px;background:var(--ink);font-size:10px}
.foot-logo{left:143px;top:3934px;color:var(--white);font-size:34px}
.foot-logo .mark{width:44px;height:44px}
.foot-col{top:3852px;color:var(--white)}
.foot-col h4{font-family:var(--head);font-weight:600;font-size:20px;letter-spacing:2px;margin-bottom:10px;white-space:nowrap}
.foot-col ul{list-style:none;font-size:14px;line-height:26.5px;padding-left:2px}
.col-menu{left:457px}
.col-info{left:625px}
.col-follow{left:879px;top:3862px}
.follow-icons{display:flex;gap:11px;margin-top:14px}
.follow-icons span{width:35px;height:35px;border-radius:50%;background:#2e2e30;display:flex;align-items:center;justify-content:center}
.follow-icons span::after{content:"";width:10px;height:10px;border-radius:2px;background:var(--white)}
.rule{left:90px;top:4130px;width:1020px;height:1px;background:#3c3c3e}
.copyright{left:0;top:4150px;width:1200px;text-align:center;color:var(--white);font-size:15px}
.to-top{left:1131px;top:4107px;width:46px;height:46px;border-radius:50%;background:var(--red);display:flex;align-items:center;justify-content:center}
</style>
</head>
<body>

<!-- hero -->
<section class="abs hero">
  <div class="abs sculpture" role="img" aria-label="Photo of a twisted metal infinity sculpture"></div>
</section>

<div class="abs topbar">
  <span class="contact">
    <svg width="12" height="12" viewBox="0 0 24 24"><path fill="#e4151b" d="M6.6 10.8a15 15 0 0 0 6.6 6.6l2.2-2.2c.3-.3.7-.4 1-.2 1.1.4 2.3.6 3.6.6.6 0 1 .4 1 1V20c0 .6-.4 1-1 1A17 17 0 0 1 3 4c0-.6.4-1 1-1h3.5c.6 0 1 .4 1 1 0 1.3.2 2.5.6 3.6.1.3 0 .7-.2 1z"/></svg>
    Call us - (001) 555-0182
  </span>
  <span class="contact">
    <svg width="12" height="10" viewBox="0 0 24 18"><path fill="#e4151b" d="M0 0h24v18H0zM2 2v1l10 7 10-7V2z"/></svg>
    info@orbelta.com
  </span>
  <span class="social"><span></span><span></span><span></span></span>
</div>

<a class="abs logo site-logo" href="#"><span class="mark"></span>ORBELTA</a>

<nav class="abs nav">
  <svg width="18" height="16" viewBox="0 0 24 22"><path fill="#e4151b" d="M12 0 0 11h3v11h7v-7h4v7h7V11h3z"/></svg>
  <a class="caret" href="#">Markets</a>
  <a class="caret" href="#">Products</a>
  <a href="#">About Us</a>
  <a class="caret" href="#">Platform</a>
  <a class="caret" href="#">Services</a>
  <a href="#">Resources</a>
</nav>
<a class="abs btn btn-nav" href="#">Schedule a demo today</a>

<div class="abs hero-kicker">WELCOME TO</div>
<h1 class="abs hero-title">ORBELTA</h1>
<p class="abs hero-sub">an infinitely composable Enterprise Applications Platform (EAP) for real estate.</p>
<a class="abs btn btn-sm btn-learn" href="#">Learn more</a>
<a class="abs btn btn-sm btn-demo" href="#">Get free demo</a>

<!-- dark: about + modules -->
<section class="abs dark"></section>

<svg class="abs about-media" viewBox="0 0 462 445" role="img" aria-label="Photo of a curved tiled building facade with a play button">
  <defs>
    <linearGradient id="facade" x1="0" y1="0" x2="1" y2="1">
      <stop offset="0" stop-color="#8fa3a8"/>
      <stop offset=".5" stop-color="#c9cdcf"/>
      <stop offset="1" stop-color="#5d6264"/>
    </linearGradient>
  </defs>
  <polygon points="231,0 347,67 347,178 462,245 462,378 347,445 231,378 115,445 0,378 0,245 115,178 115,67" fill="#4a0c0f"/>
  <polygon points="231,24 327,80 327,192 430,252 430,368 347,418 231,352 115,418 32,368 32,252 135,192 135,80" fill="#2a1214" stroke="#6e1216" stroke-width="3"/>
  <polygon points="231,44 310,90 310,200 410,258 410,360 347,396 231,330 115,396 52,360 52,258 152,200 152,90" fill="url(#facade)"/>
  <circle cx="233" cy="241" r="46" fill="rgba(40,40,42,.75)"/>
  <polygon points="224,226 224,256 248,241" fill="#fff"/>
</svg>

<div class="abs about-copy">
  <h2 class="h-section">ABOUT<br>ORBELTA</h2>
  <div class="h-sub">ONE SOLUTION - INFINITE POSSIBILITIES</div>
  <p><b>Orbelta</b> is the real estate industry's modern alternative to rigid, legacy ERP systems. With decades of real estate enterprise software development and implementation expertise — spanning hundreds of blue chip global real estate investment firms — we have a proven track record of enterprise excellence.</p>
  <p>Orbelta was born from decades of real estate enterprise software development and implementation experience — spanning hundreds of blue chip global real estate investment firms. But Orbelta is unlike anything you've experienced before.</p>
</div>

<div class="abs modules-head">
  <h2 class="h-section">THE MODULES OF ORB</h2>
  <div class="h-sub">SIMPLE - SECURE - SCALABLE</div>
  <p>Orbelta is the real estate industry's only infinitely composable Enterprise Applications Platform (EAP), ensuring scalability, security, auditability, and compliance. Orbelta is a complete solution covering all functional areas of real estate investment, development, finance, accounting, management and operations.</p>
</div>

<ul class="abs module-list">
  <li>LEASE ACTIVITY ( AUTO-CREATION )</li>
  <li>RECURRING CHARGES</li>
  <li>PORTFOLIO MANAGEMENT</li>
  <li>BILLING DASHBOARDS</li>
  <li>TRACKING</li>
  <li>CLIENT PORTAL</li>
  <li>LEAD TRACKING WITH DEFINABLE STAGES</li>
  <li>BUDGET / FORECASTING</li>
  <li class="active">METERING
    <svg width="16" height="16" viewBox="0 0 16 16"><path d="M3 13 13 3M6 3h7v7" fill="none" stroke="#e4151b" stroke-width="1.4"/></svg>
  </li>
</ul>

<div class="abs module-cube" role="img" aria-label="Illustration of the Metering module as a grey periodic-table cube"></div>

<a class="abs link-red view-modules" href="#">View all modules
  <svg width="18" height="12" viewBox="0 0 18 12"><path d="M0 6h16M11 1l5 5-5 5" fill="none" stroke="#e4151b" stroke-width="1.5"/></svg>
</a>

<!-- light: platform + team -->
<section class="abs light"></section>

<div class="abs platform-img" role="img" aria-label="Photo of a perforated metal architectural facade"></div>
<div class="abs platform-copy">
  <h2 class="h-section">PLATFORM</h2>
  <div class="h-sub">STOP SETTLING FOR LESS THAN EXACTLY<br>WHAT YOU WANT</div>
  <p>Orbelta combines the best of all worlds in our Enterprise Applications Platform (EAP): the simplicity and scalability of custom, no-code, software and the security and confidence of a complete, SOC 2 compliant industry solution. Our modular approach enables rapid innovation and re-invention of your business by casting off the shackles of legacy ERP technology and delivering a modern, agile solution that bridges the gaps for all of your real estate workflows.</p>
  <a class="btn btn-more" href="#">Read more</a>
</div>

<div class="abs team-panel"></div>
<div class="abs team-photo" role="img" aria-label="Portrait photo of the product manager"></div>
<div class="abs team-copy">
  <h2 class="h-section">ORB TEAM</h2>
  <div class="team-name">MIRA SOLENNE</div>
  <div class="team-role">Product Manager</div>
  <p>Orbelta combines the best of all worlds in our Enterprise Applications Platform (EAP): the simplicity and scalability of custom, no-code, software..</p>
  <div class="thumbs" role="img" aria-label="Portrait photos of four team members"><span></span><span></span><span></span><span></span></div>
  <a class="link-red" href="#">View all team
    <svg width="18" height="12" viewBox="0 0 18 12"><path d="M0 6h16M11 1l5 5-5 5" fill="none" stroke="#e4151b" stroke-width="1.5"/></svg>
  </a>
</div>

<!-- footer -->
<footer class="abs footer"></footer>

<div class="abs cta"></div>
<div class="abs cta-mark"></div>
<div class="abs cta-text">DISCOVER THE POWER<br>OF CUTTING-EDGE ERM<br>SOLUTIONS</div>
<a class="abs btn btn-cta" href="#">Schedule a demo today</a>

<a class="abs logo foot-logo" href="#"><span class="mark"></span>ORBELTA</a>

<div class="abs foot-col col-menu">
  <h4>MENU</h4>
  <ul><li>Home</li><li>Markets</li><li>Products</li><li>About Us</li><li>Platform</li><li>Services</li><li>Resources</li></ul>
</div>
<div class="abs foot-col col-info">
  <h4>INFORMATION</h4>
  <ul><li>Privacy Policy</li><li>Terms</li><li>Condition</li><li>Help</li><li>Contact Us</li></ul>
</div>
<div class="abs foot-col col-follow">
  <h4>FOLLOW US</h4>
  <div class="follow-icons"><span></span><span></span><span></span><span></span></div>
</div>

<div class="abs rule"></div>
<p class="abs copyright">© 2024 Orbelta. All Rights Reserved.</p>
<a class="abs to-top" href="#" aria-label="Back to top">
  <svg width="14" height="10" viewBox="0 0 14 10"><path d="M1 8 7 2l6 6" fill="none" stroke="#fff" stroke-width="2"/></svg>
</a>

</body>
</html>
```